Vellisant - Quality health delivered at your door

Vellisant offers home and Community Based Services for adults who wish to continue live independently in their communities. We increase accessibility to health care, reduce health care delivery gap, reduce mortality and morbidity, reduce health while promoting healthy living in the comfort of our patients communities or homes.

We provide on site services and deliver high quality healthcare at your door. Our experienced physicians coordinate care with our certified nurse practitioners and provide chronic care management, physical therapy, rehabilitation and medications management.

Target Market(s)

Older population living in independent living facilities

Industry/Entity Type

Health Care

Contact Information for Business Card

Vellisant

Number of Pages Required

4 page

Font styles to use
Sans Serif

Colors

Designer to choose colors to be used in the design.

```html
<!DOCTYPE html>
<html lang="en">
<head>
<meta charset="utf-8">
<title>Vellisant – Quality health delivered at your door</title>
<link rel="stylesheet" href="https://fonts.googleapis.com/css2?family=Montserrat:wght@700&family=Raleway:wght@500;600&family=Poppins:wght@400;500;600&display=swap">
<style>
:root{
  --orange:#f7990f;
  --green:#5b8a16;
  --ink:#333333;
  --muted:#8a8a8a;
  --tile:#f7f7f7;
  --band:#f4f4f4;
  --footer:#1e1e1e;
  --footer-base:#111111;
  --white:#ffffff;
}
*{box-sizing:border-box;margin:0;padding:0}
html,body{width:668px;height:1200px;overflow:hidden;background:var(--white)}
body{font-family:"Poppins",sans-serif;color:var(--ink)}
.page{position:relative;width:668px;height:1200px;overflow:hidden}
.abs{position:absolute}

/* header */
.site-header{left:0;top:0;width:668px;height:40px;background:var(--white)}
.brand{left:52px;top:9px;display:flex;align-items:center;gap:5px;font-family:"Poppins",sans-serif;font-weight:600;font-size:10px;color:var(--ink);letter-spacing:.3px}
.brand-dot{width:16px;height:16px;border-radius:50%;background:var(--orange)}
.main-nav{left:198px;top:0;display:flex;height:32px;font-size:7.2px;color:#555}
.main-nav a{color:inherit;text-decoration:none;display:flex;align-items:center;padding:0 10.5px}
.main-nav a.active{background:var(--green);color:var(--white);padding:0 8px}
.nav-toggle{left:606px;top:18px;width:7px}

/* hero */
.hero{left:0;top:40px;width:668px;height:243px;background:linear-gradient(180deg,#6c7059 0%,#8a8570 45%,#a39e8c 100%)}
.hero-shade{left:0;top:40px;width:668px;height:243px;background:rgba(40,40,30,.28)}
.hero-title{left:0;top:143px;width:668px;text-align:center;font-family:"Montserrat",sans-serif;font-weight:700;font-size:20px;line-height:31px;color:var(--white)}

/* feature cards */
.feature{width:151px;height:148px;top:246px}
.feature-photo{width:151px;height:96px}
.feature-body{width:151px;height:52px;background:var(--orange);padding:6px 13px;color:var(--white)}
.feature-body h3{font-family:"Poppins",sans-serif;font-weight:500;font-size:10px;margin-bottom:3px}
.feature-body p{font-size:5.6px;line-height:11px}

/* section headings */
.section-title{left:0;width:668px;text-align:center;font-family:"Raleway",sans-serif;font-weight:500;font-size:15px;color:var(--ink)}
.section-copy{text-align:center;font-size:5.6px;line-height:11.5px;color:var(--muted)}

/* services */
.service{width:148px;background:var(--tile);text-align:center;padding-top:9px}
.service svg{width:13px;height:13px;fill:var(--green)}
.service h4{font-family:"Raleway",sans-serif;font-weight:500;font-size:8.8px;color:var(--ink);margin:6px 0 6px}
.service p{font-size:5.6px;line-height:11px;color:var(--muted);padding:0 10px}

.btn{background:var(--orange);color:var(--white);font-family:"Raleway",sans-serif;font-weight:600;display:flex;align-items:center;justify-content:center;letter-spacing:.3px}

/* blog */
.blog-band{left:0;top:713px;width:668px;height:233px;background:var(--band)}
.post{width:158px;height:116px;top:808px}
.post-date{right:0;bottom:0;width:33px;height:28px;background:var(--orange);color:var(--white);text-align:center;font-size:12px;line-height:14px;padding-top:2px}
.post-date span{display:block;font-size:7px;line-height:9px}

/* footer */
.site-footer{left:0;top:1072px;width:668px;height:104px;background:var(--footer)}
.footer-brand{left:88px;top:1089px;width:88px;text-align:center;color:var(--white);font-size:12px;font-weight:400;letter-spacing:.3px}
.footer-brand .brand-dot{width:44px;height:44px;margin:0 auto 6px}
.footer-col{top:1090px;color:var(--white)}
.footer-col h5{font-family:"Raleway",sans-serif;font-weight:600;font-size:7.2px;margin-bottom:6px}
.footer-col li{list-style:none;font-size:5.6px;line-height:12px}
.footer-base{left:0;top:1176px;width:668px;height:24px;background:var(--footer-base);color:var(--white);font-size:5.8px;text-align:center;line-height:24px}
</style>
</head>
<body>
<div class="page">

  <header class="site-header abs">
    <div class="brand abs"><span class="brand-dot"></span>Vellisant</div>
    <nav class="main-nav abs">
      <a class="active" href="#">Home</a>
      <a href="#">Assisted Living</a>
      <a href="#">Skilled Nursing</a>
      <a href="#">Independent Living</a>
      <a href="#">Home and Community Based Services</a>
    </nav>
    <svg class="nav-toggle abs" viewBox="0 0 7 6" aria-hidden="true"><rect y="0" width="7" height="1" fill="#555"/><rect y="2.5" width="7" height="1" fill="#555"/><rect y="5" width="7" height="1" fill="#555"/></svg>
  </header>

  <div class="hero abs" role="img" aria-label="Photo of smiling older adults walking together outdoors"></div>
  <div class="hero-shade abs"></div>
  <h1 class="hero-title abs">Deliver High Quality Healthcare<br>At Your Door Step</h1>

  <article class="feature abs" style="left:82px">
    <div class="feature-photo" role="img" aria-label="Photo of an older woman writing in a notebook" style="background:linear-gradient(135deg,#dde6ee,#c9b7a0)"></div>
    <div class="feature-body"><h3>Cost Effectiveness</h3><p>Lorem Ipsum is simply dummy text of the printing and typesetting industry.</p></div>
  </article>
  <article class="feature abs" style="left:263px">
    <div class="feature-photo" role="img" aria-label="Photo of a caregiver's hand resting on an older person's hand" style="background:linear-gradient(135deg,#e9e6e4,#b58a6e 60%,#2e3e6a)"></div>
    <div class="feature-body"><h3>Culturally Responsive</h3><p>Lorem Ipsum is simply dummy text of the printing and typesetting industry.</p></div>
  </article>
  <article class="feature abs" style="left:446px">
    <div class="feature-photo" role="img" aria-label="Photo of older friends laughing together on a sofa" style="background:linear-gradient(135deg,#efe9e2,#a88f78 55%,#5c7ea8)"></div>
    <div class="feature-body"><h3>Familiarity</h3><p>Lorem Ipsum is simply dummy text of the printing and typesetting industry.</p></div>
  </article>

  <h2 class="section-title abs" style="top:413px">Welcome To&nbsp; Vellisant</h2>
  <p class="section-copy abs" style="left:92px;top:440px;width:484px">Vellisant offers home and Community Based Services for adults who wish to continue to live independently in the comfort of their communities. We provide on site services and deliver high quality healthcare at your door. Our experienced physicians coordinate care with our certified nurse practitioners and provide chronic care management, physical therapy, rehabilitation and medications management.</p>

  <section>
    <div class="service abs" style="left:96px;top:486px;height:84px">
      <svg viewBox="0 0 16 16" aria-hidden="true"><path d="M3 1h2v1H4v4a3 3 0 0 0 6 0V2H9V1h2v5a4 4 0 0 1-3.5 4v1.5a2 2 0 0 0 4 0V9.8a1.6 1.6 0 1 1 1 0v1.7a3 3 0 0 1-6 0V10A4 4 0 0 1 3 6z"/></svg>
      <h4>Mental Health</h4><p>Lorem Ipsum is simply dummy text of the printing and typesetting industry.</p>
    </div>
    <div class="service abs" style="left:261px;top:486px;height:84px">
      <svg viewBox="0 0 16 16" aria-hidden="true"><path d="M4 1c-2 0-3 2-3 4 0 3 1.5 4 2 7 .3 2 1 3 1.7 3s1-1.5 1.3-3 .6-2 2-2 1.7.5 2 2 .6 3 1.3 3 1.4-1 1.7-3c.5-3 2-4 2-7 0-2-1-4-3-4-1.5 0-2.5 1-4 1S5.5 1 4 1z"/></svg>
      <h4>Dental Health</h4><p>Lorem Ipsum is simply dummy text of the printing and typesetting industry.</p>
    </div>
    <div class="service abs" style="left:425px;top:486px;height:84px">
      <svg viewBox="0 0 16 16" aria-hidden="true"><circle cx="8" cy="2.5" r="1.8"/><path d="M2 4.5l1-.8 3 2h4l3-2 1 .8-3.5 3V15H9v-4H7v4H5.5V7.5z"/></svg>
      <h4>Physical Therapy</h4><p>Lorem Ipsum is simply dummy text of the printing and typesetting industry.</p>
    </div>
    <div class="service abs" style="left:96px;top:579px;height:82px">
      <svg viewBox="0 0 16 16" aria-hidden="true"><path d="M1 3h9v8H1zM10 6h3l2 3v2h-5z"/><circle cx="4" cy="12" r="1.6"/><circle cx="12" cy="12" r="1.6"/></svg>
      <h4>Transportation</h4><p>Lorem Ipsum is simply dummy text of the printing and typesetting industry.</p>
    </div>
    <div class="service abs" style="left:261px;top:579px;height:82px">
      <svg viewBox="0 0 16 16" aria-hidden="true"><path d="M8 15 1.8 8.8A4 4 0 0 1 8 3.5a4 4 0 0 1 6.2 5.3z"/><path d="M1 8h4l1-2 2 4 1.5-3 1 1H15" stroke="#fff" stroke-width="1" fill="none"/></svg>
      <h4>Transitional Care</h4><p>Lorem Ipsum is simply dummy text of the printing and typesetting industry.</p>
    </div>
    <div class="service abs" style="left:425px;top:579px;height:82px">
      <svg viewBox="0 0 16 16" aria-hidden="true"><path d="M7 1h2l.4 2 1.5.7 1.7-1.2 1.4 1.4-1.2 1.7.7 1.5 2 .4v2l-2 .4-.7 1.5 1.2 1.7-1.4 1.4-1.7-1.2-1.5.7L9 15H7l-.4-2-1.5-.7-1.7 1.2-1.4-1.4 1.2-1.7L2.5 9 1 9V7l2-.4.7-1.5-1.2-1.7 1.4-1.4 1.7 1.2 1.5-.7zM8 5.5a2.5 2.5 0 1 0 0 5 2.5 2.5 0 0 0 0-5z"/></svg>
      <h4>Social Services assessment</h4><p>Lorem Ipsum is simply dummy text of the printing and typesetting industry.</p>
    </div>
  </section>

  <a class="btn abs" style="left:282px;top:674px;width:104px;height:21px;font-size:9px">MORE SERVICES</a>

  <div class="blog-band abs"></div>
  <h2 class="section-title abs" style="top:731px">Check Out Our Blog</h2>
  <p class="section-copy abs" style="left:88px;top:759px;width:492px">Lorem Ipsum is simply dummy text of the printing and typesetting industry. Lorem Ipsum has been the industry's standard dummy text ever since the 1500Lorem Ipsum is simply dummy text of the printing and typesetting industry. Lorem Ipsum has been the industry's standard dummy text ever since the 1500Lorem Ipsum is simply dummy text of the printing and typesetting industry. Lorem Ipsum has been the industry.</p>

  <article class="post abs" style="left:88px" role="img" aria-label="Photo of an older woman gazing out of a window">
    <div class="abs" style="inset:0;background:linear-gradient(90deg,#e7ebe6,#9d968c 45%,#6e6a62)"></div>
    <div class="post-date abs">02<span>JUL</span></div>
  </article>
  <article class="post abs" style="left:255px" role="img" aria-label="Photo of a nurse helping an older man with a walker">
    <div class="abs" style="inset:0;background:linear-gradient(135deg,#9aa5c4,#e9e6e2 50%,#c2b19f)"></div>
    <div class="post-date abs">05<span>JUL</span></div>
  </article>
  <article class="post abs" style="left:421px" role="img" aria-label="Photo of an older couple embracing on a beach">
    <div class="abs" style="inset:0;background:linear-gradient(180deg,#6fa6c9,#c9c3b6 60%,#d8cdbb)"></div>
    <div class="post-date abs">14<span>JUL</span></div>
  </article>

  <h2 class="section-title abs" style="top:962px">Benefits Of&nbsp; Vellisant</h2>
  <p class="section-copy abs" style="left:92px;top:988px;width:484px">Lorem Ipsum is simply dummy text of the printing and typesetting industry. Lorem Ipsum has been the industry's standard dummy text ever since the 1500Lorem Ipsum is simply dummy text of the printing and typesetting industry. Lorem Ipsum has been the industry's standard dummy text ever since the 1500Lorem Ipsum is simply dummy text of the printing and typesetting industry. Lorem Ipsum has been the industry's standard.</p>
  <a class="btn abs" style="left:296px;top:1034px;width:76px;height:19px;font-size:8px">READ MORE &gt;&gt;</a>

  <footer>
    <div class="site-footer abs"></div>
    <div class="footer-brand abs"><div class="brand-dot"></div>VELLISANT</div>
    <div class="footer-col abs" style="left:245px">
      <h5>About Vellisant</h5>
      <ul><li>Ethics Policy</li><li>Find Us</li><li>How to Get Help</li><li>Jobs</li></ul>
    </div>
    <div class="footer-col abs" style="left:386px">
      <h5>Tools</h5>
      <ul><li>Acronyms</li><li>Contacts</li><li>FAQs</li><li>Glossary</li><li>Archive</li></ul>
    </div>
    <div class="footer-col abs" style="left:490px">
      <h5>Helpful Links</h5>
      <ul><li>Web Policies &amp; Important Links</li><li>Privacy Policy</li><li>Plain Language</li><li>Freedom of Information</li></ul>
    </div>
    <div class="footer-base abs">© 2017 Vellisant. All Rights Reserved.</div>
  </footer>

</div>
</body>
</html>
```